business card deign

Logo needs the following on it.
1. attached logo
2. Tagline - "If it keeps a drink cold or the party going...we do it!"
3. Name- Dalton Pikes, Founder and CPO
4. Address - 412 E. Carver Avenue, Ste 2207, Tampa, FL. 33917
5. Phone - 555.318.4726

```html
<!DOCTYPE html>
<html lang="en">
<head>
<meta charset="utf-8">
<title>Kelvaro Business Card</title>
<link href="https://fonts.googleapis.com/css2?family=Open+Sans:wght@400;600;700&family=Roboto:wght@700&display=swap" rel="stylesheet">
<style>
  :root {
    --stage: #222222;
    --card-black: #151515;
    --gold-deep: #9a6c36;
    --gold-mid: #c99a52;
    --gold-light: #f6e3a2;
    --gold-text: #c8985a;
    --ink: #1a1408;
  }
  * { box-sizing: border-box; margin: 0; padding: 0; }
  html, body { width: 1200px; height: 711px; overflow: hidden; }
  body {
    background: var(--stage);
    font-family: "Open Sans", sans-serif;
    display: flex;
    align-items: center;
    justify-content: center;
    gap: 70px;
  }
  .card {
    width: 330px;
    height: 576px;
    border-radius: 26px;
    position: relative;
    overflow: hidden;
    box-shadow: 0 18px 40px rgba(0,0,0,0.55);
  }
  .gold-surface {
    background: linear-gradient(115deg, var(--gold-deep) 0%, var(--gold-mid) 22%, var(--gold-light) 45%, var(--gold-mid) 68%, var(--gold-deep) 100%);
  }
  /* Front */
  .card-front { display: flex; align-items: center; justify-content: center; }
  .front-wordmark {
    transform: rotate(-90deg);
    font-family: "Open Sans", sans-serif;
    font-weight: 700;
    font-size: 78px;
    letter-spacing: 14px;
    color: #8a5f2c;
    white-space: nowrap;
  }
  /* Back */
  .card-back { background: var(--card-black); }
  .back-brand {
    position: absolute;
    top: 120px; left: 0; right: 0;
    text-align: center;
    font-weight: 700;
    font-size: 34px;
    letter-spacing: 12px;
    padding-left: 12px;
    color: var(--gold-text);
  }
  .identity {
    position: absolute;
    top: 268px; left: 0; right: 0;
    text-align: center;
    color: var(--gold-text);
  }
  .person-name { font-family: "Roboto", sans-serif; font-weight: 700; font-size: 30px; }
  .person-role { font-weight: 600; font-size: 17px; margin-top: 2px; }
  .divider { width: 250px; height: 1px; margin: 12px auto 12px; background: linear-gradient(90deg, transparent, var(--gold-mid), var(--gold-light), var(--gold-mid), transparent); }
  .tagline { font-size: 15px; line-height: 1.4; padding: 0 34px; }
  .contact-band {
    position: absolute;
    left: 0; right: 0; bottom: 0;
    height: 168px;
    text-align: center;
    color: var(--ink);
    padding-top: 22px;
  }
  .contact-icons { display: flex; justify-content: center; gap: 8px; margin-bottom: 12px; }
  .contact-icons svg { width: 26px; height: 26px; }
  .contact-lines { font-size: 15px; line-height: 1.35; font-weight: 400; }
</style>
</head>
<body>
  <div class="card card-front gold-surface">
    <div class="front-wordmark">KELVARO</div>
  </div>

  <div class="card card-back">
    <div class="back-brand">KELVARO</div>
    <div class="identity">
      <div class="person-name">Dalton Pikes</div>
      <div class="person-role">Founder and CPO</div>
      <div class="divider"></div>
      <p class="tagline">If it keeps a drink cold or the party going...we do it!</p>
    </div>
    <div class="contact-band gold-surface">
      <div class="contact-icons">
        <svg viewBox="0 0 26 26" aria-label="Phone">
          <circle cx="13" cy="13" r="12" fill="#7a5526"/>
          <circle cx="13" cy="13" r="10" fill="#e2c07a"/>
          <path d="M9 8.5c.6-.6 1.4-.5 1.8.1l1 1.6c.3.5.2 1-.2 1.4l-.6.5c.6 1.3 1.6 2.3 2.9 2.9l.5-.6c.4-.4.9-.5 1.4-.2l1.6 1c.6.4.7 1.2.1 1.8-1 1-2.6 1.2-4.2.3-2-1.1-3.6-2.7-4.7-4.7-.9-1.6-.7-3.2.4-4.1z" fill="#3b2a10"/>
        </svg>
        <svg viewBox="0 0 26 26" aria-label="Location">
          <circle cx="13" cy="13" r="12" fill="#7a5526"/>
          <circle cx="13" cy="13" r="10" fill="#e2c07a"/>
          <path d="M13 6.5a4.3 4.3 0 0 0-4.3 4.3c0 3.2 4.3 8 4.3 8s4.3-4.8 4.3-8A4.3 4.3 0 0 0 13 6.5zm0 6a1.7 1.7 0 1 1 0-3.4 1.7 1.7 0 0 1 0 3.4z" fill="#3b2a10"/>
        </svg>
      </div>
      <div class="contact-lines">
        <div>555.318.4726</div>
        <div>412 E. Carver Avenue,</div>
        <div>Ste 2207, Tampa, FL. 33917</div>
      </div>
    </div>
  </div>
</body>
</html>
```